New Webpage for High Class Expert Witness Services Company

We are looking for a minimalist design for a webpage that just has our logo and an entry form offer to connect with one of our Liaisons.
The entry form should just ask for Name, Email, Contact Info and Description of Project.

Company Name is: The Marlowe Crest Advisory Services

Number of Pages Required

1 page

```html
<!DOCTYPE html>
<html lang="en">
<head>
<meta charset="UTF-8">
<title>The Marlowe Crest Advisory Services — Connect with a Liaison</title>
<link rel="stylesheet" href="https://fonts.googleapis.com/css2?family=Cinzel:wght@400;500&family=Poppins:wght@400;500;600&display=swap">
<style>
  :root {
    --page-bg: #000000;
    --hero-top: #2b3140;
    --hero-bottom: #161a24;
    --card-bg: #1d1d1d;
    --card-glow: #2c2c2c;
    --card-border: #3a3a3a;
    --panel-bg: #292929;
    --footer-bg: #151515;
    --text-main: #f2f2f2;
    --text-soft: #c9c9c9;
    --text-dim: #a9a9a9;
    --field-bg: #ffffff;
    --field-text: #8a8a8a;
    --ink: #161616;
    --divider: #4a4a4a;
  }
  * { box-sizing: border-box; margin: 0; padding: 0; }
  html, body { width: 1200px; height: 1125px; overflow: hidden; background: var(--page-bg); }
  body { font-family: "Poppins", sans-serif; color: var(--text-main); position: relative; }

  .hero {
    position: absolute; left: 0; top: 0; width: 1200px; height: 388px;
    background: radial-gradient(ellipse at 60% 40%, #3a4458 0%, transparent 60%),
                linear-gradient(180deg, var(--hero-top), var(--hero-bottom));
  }
  .brand {
    position: absolute; left: 0; top: 98px; width: 1200px; text-align: center;
    font-family: "Cinzel", serif; font-weight: 500; color: #dcdcdc;
  }
  .brand-name { font-size: 44px; letter-spacing: 1px; line-height: 1.1; display: block; }
  .brand-sub { font-size: 24px; letter-spacing: 6px; line-height: 1.4; display: block; }

  .contact-card {
    position: absolute; left: 141px; top: 315px; width: 918px; height: 662px;
    border: 1px solid var(--card-border); border-radius: 14px;
    background: radial-gradient(ellipse at 15% 55%, var(--card-glow) 0%, var(--card-bg) 55%);
  }

  .intro { position: absolute; left: 61px; top: 80px; width: 322px; }
  .section-title { font-family: "Cinzel", serif; font-weight: 400; font-size: 36px; line-height: 1; color: var(--text-main); }
  .intro-text { margin-top: 14px; font-size: 13.5px; line-height: 19px; color: var(--text-soft); }

  .feature { position: absolute; left: 61px; width: 322px; height: 60px; }
  .feature-icon {
    position: absolute; left: 0; top: 0; width: 49px; height: 49px; border-radius: 50%;
    background: #fff; display: flex; align-items: center; justify-content: center;
  }
  .feature-title { position: absolute; left: 66px; top: 1px; font-size: 15px; font-weight: 600; color: #e8e8e8; }
  .feature-text { position: absolute; left: 66px; top: 26px; width: 260px; font-size: 13.5px; line-height: 19px; color: var(--text-soft); }

  .divider { position: absolute; left: 61px; top: 487px; width: 319px; height: 1px; background: var(--divider); }
  .social-title { position: absolute; left: 61px; top: 515px; font-size: 15px; font-weight: 500; color: #dcdcdc; }
  .social-list { position: absolute; left: 61px; top: 553px; display: flex; gap: 16px; list-style: none; }
  .social-dot { width: 32px; height: 32px; border-radius: 50%; border: 2px solid #8f8f8f; }
  .social-dot.is-active { background: #fff; border-color: #fff; }

  .message-panel {
    position: absolute; left: 436px; top: 59px; width: 421px; height: 542px;
    background: var(--panel-bg); border-radius: 12px;
  }
  .message-panel .section-title { position: absolute; left: 33px; top: 33px; font-size: 30px; }
  .field-label { position: absolute; left: 35px; font-size: 13px; color: #d6d6d6; }
  .field {
    position: absolute; left: 33px; width: 353px; height: 42px; border-radius: 6px;
    background: var(--field-bg); color: var(--field-text); font-size: 13px;
    padding: 0 16px; display: flex; align-items: center; justify-content: space-between;
  }
  .field.is-textarea { height: 84px; align-items: flex-start; padding-top: 11px; }
  .submit {
    position: absolute; left: 33px; top: 463px; width: 353px; height: 45px; border-radius: 6px;
    background: #fff; color: var(--ink); font-size: 13px; font-weight: 400; letter-spacing: 0.2px;
    display: flex; align-items: center; justify-content: center; gap: 10px; border: none;
    font-family: "Poppins", sans-serif;
  }

  .site-footer {
    position: absolute; left: 0; top: 1055px; width: 1200px; height: 70px; background: var(--footer-bg);
    display: flex; align-items: center; justify-content: center; font-size: 14px; color: #e6e6e6;
  }
</style>
</head>
<body>
  <header class="hero" role="img" aria-label="Dimmed photo of medical laboratory equipment overlaid with connected healthcare icons"></header>
  <div class="brand">
    <span class="brand-name">THE MARLOWE CREST</span>
    <span class="brand-sub">ADVISORY SERVICES</span>
  </div>

  <main class="contact-card">
    <section class="intro">
      <h1 class="section-title">GET IN TOUCH</h1>
      <p class="intro-text">Lorem ipsum dolor amet, consectetuer adipiscing elit. Aenean commodo ligula eget dolor.</p>
    </section>

    <div class="feature" style="top:193px">
      <div class="feature-icon">
        <svg width="24" height="26" viewBox="0 0 24 26"><path d="M12 1 L22 5 V12 C22 18 17.5 23 12 25 C6.5 23 2 18 2 12 V5 Z" fill="#3a3a3a"/><path d="M7.5 13 L10.8 16 L16.5 9.5" stroke="#fff" stroke-width="2" fill="none" stroke-linecap="round" stroke-linejoin="round"/></svg>
      </div>
      <h3 class="feature-title">Allied-grade confidentiality</h3>
      <p class="feature-text">Aenean massa. Cum sociis natoque penatibus et magnis parturient montes.</p>
    </div>

    <div class="feature" style="top:293px">
      <div class="feature-icon">
        <svg width="26" height="26" viewBox="0 0 26 26"><path d="M13 1 L16 3.5 L20 3 L21 7 L24.5 9 L23 13 L24.5 17 L21 19 L20 23 L16 22.5 L13 25 L10 22.5 L6 23 L5 19 L1.5 17 L3 13 L1.5 9 L5 7 L6 3 L10 3.5 Z" fill="#3a3a3a"/><path d="M8.5 13.2 L11.6 16 L17.5 10" stroke="#fff" stroke-width="2" fill="none" stroke-linecap="round" stroke-linejoin="round"/></svg>
      </div>
      <h3 class="feature-title">30+ expert witnesses</h3>
      <p class="feature-text">Aenean massa. Cum sociis natoque penatibus et magnis parturient montes.</p>
    </div>

    <div class="feature" style="top:393px">
      <div class="feature-icon">
        <svg width="26" height="26" viewBox="0 0 26 26" fill="none" stroke="#333" stroke-width="2"><circle cx="13" cy="13" r="11"/><ellipse cx="13" cy="13" rx="5" ry="11"/><line x1="2" y1="13" x2="24" y2="13"/><path d="M4 7.5 H22 M4 18.5 H22"/></svg>
      </div>
      <h3 class="feature-title">Global defense network</h3>
      <p class="feature-text">Aenean massa. Cum sociis natoque penatibus et magnis parturient montes.</p>
    </div>

    <div class="divider"></div>
    <h3 class="social-title">Follow our social media</h3>
    <ul class="social-list" aria-label="Social media links">
      <li class="social-dot is-active"></li>
      <li class="social-dot"></li>
      <li class="social-dot"></li>
      <li class="social-dot"></li>
    </ul>

    <form class="message-panel">
      <h2 class="section-title">SEND US MESSAGE</h2>

      <label class="field-label" style="top:85px">Your Name</label>
      <div class="field" style="top:105px">Enter your name
        <svg width="18" height="18" viewBox="0 0 18 18" fill="none" stroke="#222" stroke-width="1.4"><circle cx="9" cy="5.5" r="4"/><path d="M2 17 C2 12.5 5 10.5 9 10.5 C13 10.5 16 12.5 16 17"/></svg>
      </div>

      <label class="field-label" style="top:167px">Your Email</label>
      <div class="field" style="top:187px">Enter your Email
        <svg width="20" height="16" viewBox="0 0 20 16" fill="none" stroke="#222" stroke-width="1.3"><rect x="1" y="1.5" width="18" height="13" rx="1"/><path d="M1 2 L10 9.5 L19 2 M1 14 L7.5 7.5 M19 14 L12.5 7.5"/></svg>
      </div>

      <label class="field-label" style="top:249px">Your Contact</label>
      <div class="field" style="top:269px">Enter your Contact
        <svg width="18" height="18" viewBox="0 0 18 18" fill="none" stroke="#222" stroke-width="1.3" stroke-linecap="round"><path d="M4 1.5 L6.5 5 L5 7 C6 9.5 8.5 12 11 13 L13 11.5 L16.5 14 L15 16.5 C8 16.5 1.5 10 1.5 3 Z"/><path d="M10.5 4 A4 4 0 0 1 14 7.5 M10.5 1 A7 7 0 0 1 17 7.5"/></svg>
      </div>

      <label class="field-label" style="top:331px">Description of Project</label>
      <div class="field is-textarea" style="top:351px">Enter here...
        <svg width="19" height="19" viewBox="0 0 19 19" fill="none" stroke="#222" stroke-width="1.4"><path d="M9.5 1.5 A8 8 0 1 1 2.7 13.7 L1.5 17.5 L5.3 16.3 A8 8 0 0 0 9.5 17.5"/><circle cx="6" cy="9.5" r="0.6" fill="#222"/><circle cx="9.5" cy="9.5" r="0.6" fill="#222"/><circle cx="13" cy="9.5" r="0.6" fill="#222"/></svg>
      </div>

      <button class="submit" type="button">CONNECT WITH A LIAISON
        <svg width="22" height="12" viewBox="0 0 22 12" fill="none" stroke="#161616" stroke-width="2" stroke-linecap="round" stroke-linejoin="round"><path d="M1 6 H20 M15 1 L20 6 L15 11"/></svg>
      </button>
    </form>
  </main>

  <footer class="site-footer">© 2026 the marlowe crest advisory services all right</footer>
</body>
</html>
```